Stationery Design Project

We need a stationery design for our Norwegian trucking company. We have existed for about 15 years and our 12 drivers uses relatively new vehicles to transport goods around in northern Norway. Long distance routes with fresh fish og food transport is our main operations.

We have already made alogo that's printed on our trucks. The logo and a picture of our trucks is attached. I think the logo i crappy, but since its already in use, changing it is not an option in this round. Still using a better colour scheme in the overall stationery and more interesting fonts is possible (altso in the logo).

Company details:
Name: Kjelvraket AS
Organisation nr 873 615 309
Post adress: 8642 Raudvik

I like minimalism and simplicity. I am avalibly for questions in normal GMT working hours either here or on mail: ivar@fjordlast.no

Reason: Hi. Im extending the deadline because I needed some time to find a vector file of our logo. Sorry for the inconvenience

Hi, and thanks for all your interest in the project. Some updates:

-          I have decided to commit to using one of the designs. Some designer will get the payment.

-          I have extended the deadline with 24 hours since I needed some time to find our firms vector logo (a slow Swedish man was holding me up)

-          We will not choose a design before the deadline. No need to rush.

-          We have received a lot of great design and think there is a need to specified the product we want to make:

o   Business Card for all our employers. I just need the design and will duplicate with the correct numbers and name myself. The information on should be: Logo, employer’s name, Phone number, email, website, Postal number and address. Use this as a template: logo, Leif Brattvoll, 47382066, Leif@fjordlast.no,, fjordlast.no, 8642 Raudvik. The order and placement of the information is your creative decision.

o   Stickers to put on the goods we travel. On the sticker the should be the following information: Logo, phone number, Tekst and link: Fraktæ av Kjelvraket. Ke du syns? Fjordlast.no/tilbakemelding (this means: Handled by Kjelvraket. What do you think Fjordlast.no/feedback -à the link will be a feedback form). The placement the information and size is your creative decision with some stings: we have been thinking of using Drukko for printing and see that a size about 6x6 cm, 8x5 or something like that. (with 3000 copies our budget is 200 punds). Any suggestions of other suppliers are welcome. Drukko price calculator http://www.drukkolabelhouse.co.uk/digital-litho-printing/printing-labels-tags/stickers/

o   Letterhead with logo, address, phone number and organizational number.

o   Envelopes with logo,address, phone number and organizational number.

Have a nice day.

 

 

• Using the blue colour in the logo and using a similar graphic approch.

```html
<!DOCTYPE html>
<html lang="no">
<head>
<meta charset="utf-8">
<title>Kjelvraket – visittkort</title>
<link rel="stylesheet" href="https://fonts.googleapis.com/css2?family=Saira:wght@400;600&display=swap">
<style>
  :root {
    --page-bg: #e6eaee;
    --card-bg: #ffffff;
    --navy: #123a8f;
    --blue: #2f86d6;
    --sky: #3f95e0;
    --ink: #2a2f38;
    --rule: #2c4aa0;
  }
  * { box-sizing: border-box; margin: 0; padding: 0; }
  html, body {
    width: 1200px; height: 960px; overflow: hidden;
    background: var(--page-bg);
    font-family: "Saira", "Helvetica Neue", Arial, sans-serif;
  }
  .sheet {
    position: relative; width: 1200px; height: 960px;
    display: flex; flex-direction: column; align-items: center;
    justify-content: center; gap: 40px;
  }
  .card {
    position: relative; width: 700px; height: 400px;
    background: var(--card-bg);
    box-shadow: 0 6px 18px rgba(20, 40, 70, 0.18);
    overflow: hidden;
  }
  .card__accent {
    position: absolute; top: 0; bottom: 0; width: 170px;
  }
  .card--front .card__accent {
    right: 0;
    background: linear-gradient(180deg, var(--sky) 0%, var(--blue) 45%, var(--navy) 100%);
  }
  .card--back .card__accent {
    left: 0;
    background: linear-gradient(180deg, var(--sky) 0%, var(--blue) 45%, var(--navy) 100%);
  }
  .wordmark {
    position: absolute;
    font-weight: 600; color: var(--navy);
    letter-spacing: 0.5px; line-height: 1;
  }
  .card--front .wordmark { left: 44px; top: 62px; font-size: 42px; }
  .card--back .wordmark { left: 300px; top: 176px; font-size: 50px; }
  .holder {
    position: absolute; left: 48px; top: 228px;
    font-size: 30px; font-weight: 400; color: var(--ink);
  }
  .holder__rule {
    position: absolute; left: 48px; top: 292px; width: 396px; height: 1.5px;
    background: var(--rule);
  }
  .contacts {
    position: absolute; left: 48px; top: 312px;
    display: grid; grid-template-columns: 230px 200px; row-gap: 12px;
    list-style: none;
  }
  .contacts__item {
    display: flex; align-items: center; gap: 12px;
    font-size: 17px; color: var(--ink);
  }
  .contacts__icon { width: 16px; height: 16px; flex: none; fill: var(--navy); }
</style>
</head>
<body>
<main class="sheet">
  <section class="card card--front" aria-label="Visittkort forside">
    <div class="card__accent" role="img" aria-label="Blå dekorativ bue langs høyre kant"></div>
    <div class="wordmark">Kjelvraket</div>
    <h1 class="holder">Leif Brattvoll</h1>
    <div class="holder__rule"></div>
    <ul class="contacts">
      <li class="contacts__item">
        <svg class="contacts__icon" viewBox="0 0 16 16" aria-hidden="true"><rect x="1" y="1" width="14" height="14" rx="2"/><rect x="4" y="4" width="8" height="3" fill="#fff"/><rect x="4" y="9" width="2" height="2" fill="#fff"/><rect x="7" y="9" width="2" height="2" fill="#fff"/><rect x="10" y="9" width="2" height="2" fill="#fff"/></svg>
        <span>873 615 309</span>
      </li>
      <li class="contacts__item">
        <svg class="contacts__icon" viewBox="0 0 16 16" aria-hidden="true"><path d="M8 0C5 0 3 2.2 3 5c0 3.6 5 11 5 11s5-7.4 5-11c0-2.8-2-5-5-5Zm0 7a2 2 0 1 1 0-4 2 2 0 0 1 0 4Z"/></svg>
        <span>8642 Raudvik</span>
      </li>
      <li class="contacts__item">
        <svg class="contacts__icon" viewBox="0 0 16 16" aria-hidden="true"><path d="M1 6L8 1L15 6V15H1Z"/><path d="M2 7L8 11L14 7" fill="none" stroke="#fff" stroke-width="1.4"/></svg>
        <span>Leif@fjordlast.no</span>
      </li>
      <li class="contacts__item">
        <svg class="contacts__icon" viewBox="0 0 16 16" aria-hidden="true"><circle cx="8" cy="8" r="7.5"/><path d="M3 5c2 0 3 1 2.5 3S7 11 8 14M11 2.5c-1 1.5 0 3 2 3.5" fill="none" stroke="#fff" stroke-width="1.4"/></svg>
        <span>www.fjordlast.no</span>
      </li>
    </ul>
  </section>

  <section class="card card--back" aria-label="Visittkort bakside">
    <div class="card__accent" role="img" aria-label="Blå dekorativ bue langs venstre kant"></div>
    <div class="wordmark">Kjelvraket</div>
  </section>
</main>
</body>
</html>
```